Varelko App for Smart Devices IoT WiFi Electronic

Varelko is a siren manufacturer. This application is used for the company's products that have a Wi-Fi connection and an internet connection, which can be configured and activated remotely through this application. In addition, this application is used to activate the siren at specific times for the start and end of shifts in companies and schools. Users will be siren installers and IT or HR managers.
In addition to activating motorized sirens timers, some siren models have speakers and allow you to play TTS (text to speech) audio, audio recorded by the user on the phone and upload audio (mp3) with playlist programming with start and end times.
Application screens: home with dashboard (one dashboard for each category). Device categories: timers, speakers, motorized siren. Screen for requesting evaluation in the Appvista store. Screen for registering the user profile. Screen for registering devices according to their category (timers, speakers, motorized siren). Screen for registering device groups. Screen for pairing the device on the client's Wi-Fi network. Screen for registering activation times. Screen for uploading MP3 audios. Screen for registering playlists with audio selection, start and end times. Screen for recording audio for later sending to the speakers. Screen for converting text to speech and sending to the speakers. It is important to have a time picker with the day of the week to program the activation times and playlist.

Target Market(s)

Schools, Companies and Stores.

Industry/Entity Type

IoT

Font styles to use
Sans Serif
Other font styles liked:
• roboto

Colors
FFC000
F8CF3A
FAE287
FDF2CF
FEFAEE

Requirements
Must have
• time picker with weekdays for timer programming feature.
Nice to have
• app review request screen on Appvista store

```html
<!DOCTYPE html>
<html lang="en">
<head>
<meta charset="utf-8">
<title>Varelko App Screens</title>
<link rel="stylesheet" href="https://fonts.googleapis.com/css2?family=Roboto:wght@400;500;700&display=swap">
<style>
:root{
  --yellow:#FFC000;
  --yellow-soft:#F8CF3A;
  --yellow-pale:#FAE287;
  --cream:#FDF2CF;
  --ivory:#FEFAEE;
  --screen:#F4F4F4;
  --ink:#1A1A1A;
  --muted:#8A8A8A;
  --line:#D9D9D9;
  --stage-top:#606060;
  --stage-bottom:#383838;
}
*{box-sizing:border-box;margin:0;padding:0}
html,body{width:730px;height:1200px;overflow:hidden}
body{background:linear-gradient(180deg,var(--stage-top),var(--stage-bottom));font-family:"Roboto",Arial,sans-serif;color:var(--ink)}
.board{position:absolute;left:0;top:0;width:1500px;height:2464px;transform:scale(.48667);transform-origin:0 0}
.screen{position:absolute;width:255px;height:553px;background:var(--screen);overflow:hidden}
.screen *{position:absolute}
.status{left:0;top:0;width:255px;height:28px;background:var(--yellow)}
.status .time{left:22px;top:8px;font-size:10px;font-weight:500}
.status .sys{right:14px;top:9px;width:44px;height:10px}
.brand{left:0;width:100%;text-align:center;color:var(--yellow);font-weight:500;letter-spacing:.5px}
.title{left:0;width:100%;text-align:center;font-size:15px;font-weight:500;color:#2b2b2b}
.close{right:12px;top:38px;width:18px;height:18px}
.field{left:31px;width:193px}
.field .label{position:static;display:block;font-size:10px;font-weight:500;margin-bottom:2px}
.input{position:relative!important;display:block;width:193px;height:23px;border-radius:12px;background:var(--screen);box-shadow:inset 0 0 0 1px var(--line),0 1px 2px rgba(0,0,0,.08);font-size:8px;color:var(--muted);line-height:23px;padding-left:12px}
.select{position:relative!important;display:block;height:24px;border-radius:12px;background:var(--screen);box-shadow:inset 0 0 0 1px var(--line),0 2px 3px rgba(0,0,0,.1);font-size:10px;font-weight:500;line-height:24px;padding-left:16px}
.select svg{position:absolute;right:12px;top:9px;width:9px;height:6px}
.btn{height:26px;border-radius:13px;background:var(--yellow);box-shadow:0 2px 3px rgba(0,0,0,.2);text-align:center;line-height:26px;font-size:12px;font-weight:500;color:#1d1d1d}
.social{left:31px;width:195px;height:25px;border-radius:13px;background:#fafafa;box-shadow:0 1px 3px rgba(0,0,0,.22);font-size:8px;font-weight:500;line-height:25px;padding-left:62px}
.social .dot{left:40px;top:6px;width:13px;height:13px;border-radius:50%}
.dot--nimbus{background:var(--yellow-soft)}
.dot--orchard{background:#1d1d1d}
.divider{left:0;width:100%;height:12px;font-size:9px;font-weight:500;text-align:center}
.divider::before{content:"";position:absolute;left:0;right:0;top:6px;border-top:1px dashed #777}
.divider span{position:relative;background:var(--screen);padding:0 6px}
.foot{left:0;bottom:0;width:255px;height:21px;background:var(--yellow)}
.home-bar{left:82px;bottom:6px;width:90px;height:3px;border-radius:2px;background:#555}
.nav{left:0;bottom:0;width:255px;height:40px;background:var(--yellow)}
.nav .ico{top:10px;width:20px;height:20px;color:#555}
.nav-active{width:34px;height:34px;border-radius:50%;background:var(--yellow);box-shadow:0 0 0 4px var(--screen),0 3px 5px rgba(0,0,0,.25);bottom:24px;color:#1d1d1d}
.nav-active svg{left:7px;top:7px;width:20px;height:20px}
.card{border-radius:12px;background:var(--screen);box-shadow:0 3px 6px rgba(0,0,0,.14),inset 0 0 0 1px #e6e6e6}
.clock-time{left:0;width:100%;text-align:center;font-weight:700}
.clock-time small{position:static;font-size:16px;font-weight:500;margin-left:2px}
.days{left:0;width:100%;text-align:center;font-size:9px;color:var(--muted)}
.small-label{left:0;width:100%;text-align:center;font-size:10px;font-weight:500;color:#333}
.plus{left:197px;top:449px;width:28px;height:28px;border-radius:50%;background:var(--screen);box-shadow:0 2px 4px rgba(0,0,0,.25)}
.plus svg{left:6px;top:6px;width:16px;height:16px}
.hero{left:65px;width:126px;height:126px;border-radius:50%;background:radial-gradient(circle at 50% 40%,var(--yellow-soft),var(--yellow));box-shadow:0 0 22px 8px rgba(255,192,0,.45)}
.hero svg{left:33px;top:26px;width:60px;height:60px;color:#1d1d1d}
.hero .tap{left:0;width:100%;top:94px;text-align:center;font-size:8px;color:#6b5500}
.slider{height:14px;border-radius:7px;background:#fff;box-shadow:inset 0 0 0 1px var(--line)}
.slider .fill{left:0;top:0;height:14px;border-radius:7px;background:var(--yellow)}
.slider .knob{top:-1px;width:16px;height:16px;border-radius:50%;background:var(--yellow);box-shadow:0 1px 2px rgba(0,0,0,.3)}
.slider .knob svg{left:3px;top:3px;width:10px;height:10px}
.day{top:315px;height:18px;border-radius:6px;font-size:8px;font-weight:500;line-height:18px;text-align:center;box-shadow:0 1px 2px rgba(0,0,0,.2)}
.day--on{background:var(--yellow)}
.day--off{background:#fafafa;box-shadow:inset 0 0 0 1px var(--line),0 1px 2px rgba(0,0,0,.15)}
.tile{top:358px;width:52px;height:52px;border-radius:6px;background:#fafafa;box-shadow:0 2px 4px rgba(0,0,0,.2)}
.tile--on{background:var(--yellow)}
.tile svg{left:14px;top:7px;width:24px;height:24px}
.tile span{left:0;width:100%;top:38px;text-align:center;font-size:7px}
.wave{left:22px;width:212px;height:14px}
.wave .play{left:0;top:2px;width:11px;height:11px;color:#777}
.wave .bars{left:16px;top:0;width:172px;height:14px}
.wave .dur{right:0;top:2px;font-size:8px;color:var(--muted)}
.caption{left:0;width:100%;text-align:center;font-size:7px;color:var(--muted)}
.kb{left:0;top:335px;width:255px;height:218px;background:var(--yellow)}
.kb .suggest{left:0;top:0;width:255px;height:24px;display:flex}
.kb .suggest span{position:static;flex:1;text-align:center;font-size:10px;line-height:24px}
.kb .suggest .pick{background:#F7A400;color:#1d1d1d}
.kb .row{left:3px;width:249px;height:24px;display:flex;gap:3px;justify-content:center}
.kb .key{position:static;width:22px;height:24px;border-radius:4px;background:#fff;box-shadow:0 1px 0 rgba(0,0,0,.3);font-size:13px;line-height:23px;text-align:center}
.kb .key--fn{background:#F7A400;width:30px;font-size:9px}
.kb .key--wide{width:125px;font-size:9px}
.kb .key--action{width:58px;font-size:9px;background:#F7A400}
.kb .extra{top:188px;width:16px;height:16px;color:#555}
.tts-box{left:32px;top:160px;width:192px;height:140px;border-radius:10px;background:var(--screen);box-shadow:inset 0 0 0 1px var(--line),0 2px 4px rgba(0,0,0,.12);font-size:9px;line-height:12px;padding:6px 8px}
.tts-box p{position:static}
.rate-card{left:20px;top:186px;width:216px;height:130px;border-radius:14px;background:var(--screen);box-shadow:0 3px 7px rgba(0,0,0,.15),inset 0 0 0 1px #e7e7e7}
.stars{left:22px;top:52px;width:172px;height:30px}
.feature-mark{left:720px;top:1060px;width:720px;text-align:center;font-size:188px;font-weight:500;color:var(--yellow);letter-spacing:2px;line-height:1}
</style>
</head>
<body>
<svg width="0" height="0" style="position:absolute">
  <defs>
    <symbol id="i-watch" viewBox="0 0 24 24"><g fill="none" stroke="currentColor" stroke-width="2" stroke-linecap="round"><circle cx="12" cy="14" r="8"/><path d="M9 2.5h6M12 2.5V6M12 14V9.5M18.5 7l1.5-1.5"/></g></symbol>
    <symbol id="i-siren" viewBox="0 0 24 24"><g fill="none" stroke="currentColor" stroke-width="2" stroke-linecap="round"><path d="M6 18v-3a6 6 0 0 1 12 0v3"/><rect x="3.5" y="18" width="17" height="3.5" rx="1.2"/><path d="M12 2.5v2M4.5 5.5L6 7M19.5 5.5L18 7M12 15l2.5-3"/></g></symbol>
    <symbol id="i-speaker" viewBox="0 0 24 24"><g fill="none" stroke="currentColor" stroke-width="2" stroke-linejoin="round" stroke-linecap="round"><path d="M3 9h4l6-5v16l-6-5H3z"/><path d="M16 9.5a3.5 3.5 0 0 1 0 5M18.5 7a7 7 0 0 1 0 10"/></g></symbol>
    <symbol id="i-speaker-fill" viewBox="0 0 24 24"><path fill="currentColor" d="M3 9h4l6-5v16l-6-5H3z"/><path fill="none" stroke="currentColor" stroke-width="2" stroke-linecap="round" d="M16 9.5a3.5 3.5 0 0 1 0 5"/></symbol>
    <symbol id="i-note" viewBox="0 0 24 24"><path fill="currentColor" d="M9 4l12-2v13.5a3.5 3.5 0 1 1-2.5-3.35V7L11 8.3V18a3.5 3.5 0 1 1-2-3.15z"/></symbol>
    <symbol id="i-mic" viewBox="0 0 24 24"><rect x="8.5" y="2" width="7" height="12.5" rx="3.5" fill="currentColor"/><g fill="none" stroke="currentColor" stroke-width="2" stroke-linecap="round"><path d="M5.5 11a6.5 6.5 0 0 0 13 0M12 17.5V21M8.5 21.5h7"/></g></symbol>
    <symbol id="i-tts" viewBox="0 0 24 24"><g fill="none" stroke="currentColor" stroke-width="1.8" stroke-linejoin="round" stroke-linecap="round"><path d="M3 5h10v16H3z"/><path d="M5.5 10h5M5.5 13h5M5.5 16h4"/><path d="M13 8h2l3-3v12l-3-3h-2"/><path d="M20 8.5a4 4 0 0 1 0 5"/></g></symbol>
    <symbol id="i-close" viewBox="0 0 24 24"><path d="M4 4l16 16M20 4L4 20" stroke="currentColor" stroke-width="3" stroke-linecap="round"/></symbol>
    <symbol id="i-plus" viewBox="0 0 24 24"><path d="M12 3v18M3 12h18" stroke="currentColor" stroke-width="2.5" stroke-linecap="round"/></symbol>
    <symbol id="i-upload" viewBox="0 0 24 24"><g fill="none" stroke="currentColor" stroke-width="2" stroke-linecap="round"><path d="M12 15V4M7.5 8.5L12 4l4.5 4.5M4 15v5h16v-5"/></g></symbol>
    <symbol id="i-caret" viewBox="0 0 10 6"><path d="M0 0h10L5 6z" fill="currentColor"/></symbol>
    <symbol id="i-play" viewBox="0 0 10 10"><path d="M1 0l9 5-9 5z" fill="currentColor"/></symbol>
    <symbol id="i-star" viewBox="0 0 24 24"><path fill="#FFC000" d="M12 1.5l3.2 6.9 7.3.8-5.5 5 1.6 7.3L12 17.8l-6.6 3.7L7 14.2l-5.5-5 7.3-.8z"/></symbol>
    <symbol id="i-sys" viewBox="0 0 44 10"><g fill="#1a1a1a"><rect x="0" y="6" width="2" height="3"/><rect x="3" y="4.5" width="2" height="4.5"/><rect x="6" y="3" width="2" height="6"/><path d="M14 4a7 7 0 0 1 9 0l-1.2 1.3a5 5 0 0 0-6.6 0zM16.2 6.3a3.6 3.6 0 0 1 4.6 0L18.5 9z"/><rect x="28" y="1.5" width="15" height="7" rx="2"/></g></symbol>
    <pattern id="wave-bars" width="24" height="14" patternUnits="userSpaceOnUse"><g fill="#8d8d8d"><rect x="0" y="3" width="1" height="8"/><rect x="3" y="5" width="1" height="4"/><rect x="6" y="1" width="1" height="12"/><rect x="9" y="4" width="1" height="6"/><rect x="12" y="2" width="1" height="10"/><rect x="15" y="5.5" width="1" height="3"/><rect x="18" y="0" width="1" height="14"/><rect x="21" y="4" width="1" height="6"/></g></pattern>
  </defs>
</svg>

<main class="board">

  <!-- Splash -->
  <section class="screen" style="left:46px;top:39px;background:var(--screen)">
    <div class="brand" style="top:228px;font-size:58px">Varelko</div>
  </section>

  <!-- Create profile -->
  <section class="screen" style="left:334px;top:39px">
    <div class="status"><span class="time">9:41</span><svg class="sys"><use href="#i-sys"/></svg></div>
    <div class="brand" style="top:48px;font-size:30px">Varelko</div>
    <div class="title" style="top:110px">Create Your Profile</div>
    <div class="field" style="top:141px"><span class="label">Username</span><span class="input">Enter your username...</span></div>
    <div class="field" style="top:182px"><span class="label">Email</span><span class="input">Enter your Email ID...</span></div>
    <div class="field" style="top:223px"><span class="label">Password</span><span class="input">Enter your password...</span></div>
    <div class="field" style="top:264px"><span class="label">Confirm Password</span><span class="input">Confirm your password...</span></div>
    <div class="divider" style="top:313px"><span>OR</span></div>
    <div class="social" style="top:337px"><span class="dot dot--nimbus"></span>Continue with Nimbus</div>
    <div class="social" style="top:369px"><span class="dot dot--orchard"></span>Continue with Orchard</div>
    <div class="btn" style="left:63px;top:422px;width:130px">Create profile</div>
    <div class="foot"></div><div class="home-bar"></div>
  </section>

  <!-- Login -->
  <section class="screen" style="left:622px;top:39px">
    <div class="status"><span class="time">9:41</span><svg class="sys"><use href="#i-sys"/></svg></div>
    <div class="brand" style="top:48px;font-size:30px">Varelko</div>
    <div class="title" style="top:107px">Login</div>
    <div class="field" style="top:153px;left:36px"><span class="label">Username or Email ID</span><span class="input">Enter your username or Email ID...</span></div>
    <div class="field" style="top:194px;left:36px"><span class="label">Password</span><span class="input">Enter your password...</span></div>
    <div class="divider" style="top:259px"><span>OR</span></div>
    <div class="social" style="top:293px;left:36px"><span class="dot dot--nimbus"></span>Continue with Nimbus</div>
    <div class="social" style="top:325px;left:36px"><span class="dot dot--orchard"></span>Continue with Orchard</div>
    <div class="btn" style="left:63px;top:381px;width:130px">Login</div>
    <div class="foot"></div><div class="home-bar"></div>
  </section>

  <!-- Rating request -->
  <section class="screen" style="left:910px;top:39px">
    <div class="status"><span class="time">9:41</span><svg class="sys"><use href="#i-sys"/></svg></div>
    <svg class="close"><use href="#i-close"/></svg>
    <div class="brand" style="top:101px;font-size:30px">Varelko</div>
    <div class="rate-card">
      <div class="small-label" style="top:9px;font-size:11px">Tell us !</div>
      <div class="small-label" style="top:24px;font-size:11px">How do you like our app?</div>
      <svg class="stars" viewBox="0 0 172 30">
        <use href="#i-star" x="0" y="2" width="28" height="28"/><use href="#i-star" x="36" y="0" width="28" height="28"/><use href="#i-star" x="72" y="-2" width="28" height="28"/><use href="#i-star" x="108" y="0" width="28" height="28"/><use href="#i-star" x="144" y="2" width="28" height="28"/>
      </svg>
      <div style="left:85px;top:91px;width:46px;height:4px;border-radius:2px;background:var(--yellow)"></div>
      <div class="small-label" style="top:106px;font-size:8px">Rate us on Appvista store.</div>
    </div>
    <div class="btn" style="left:63px;top:355px;width:130px">Rate us !</div>
    <div class="foot"></div><div class="home-bar"></div>
  </section>

  <!-- Timer dashboard -->
  <section class="screen" style="left:46px;top:635px">
    <div class="status"><span class="time">9:41</span><svg class="sys"><use href="#i-sys"/></svg></div>
    <div class="title" style="top:38px">Timer</div>
    <svg style="left:98px;top:102px;width:60px;height:60px"><use href="#i-watch"/></svg>
    <div class="card" style="left:42px;top:184px;width:182px;height:72px">
      <div class="clock-time" style="top:2px;font-size:50px">10:00<small>AM</small></div>
      <div class="days" style="top:54px">Mon, tue, wed, thu, fri</div>
    </div>
    <div class="card" style="left:42px;top:278px;width:182px;height:72px">
      <div class="clock-time" style="top:2px;font-size:50px">05:00<small>PM</small></div>
      <div class="days" style="top:54px">Mon, tue, wed, thu, fri</div>
    </div>
    <div class="small-label" style="top:392px">Select a Preset</div>
    <div style="left:42px;top:406px;width:180px"><span class="select" style="text-align:center;padding-left:0">Preset 1<svg><use href="#i-caret"/></svg></span></div>
    <div class="plus"><svg><use href="#i-plus"/></svg></div>
    <nav class="nav">
      <svg class="ico" style="left:118px"><use href="#i-siren"/></svg>
      <svg class="ico" style="left:186px"><use href="#i-speaker"/></svg>
    </nav>
    <div class="nav-active" style="left:41px"><svg><use href="#i-watch"/></svg></div>
    <div class="home-bar" style="background:#666"></div>
  </section>

  <!-- Add timer -->
  <section class="screen" style="left:334px;top:635px">
    <div class="status"><span class="time">9:41</span><svg class="sys"><use href="#i-sys"/></svg></div>
    <div class="title" style="top:38px">Add Timer</div>
    <svg class="close"><use href="#i-close"/></svg>
    <div class="small-label" style="top:85px">Select Time</div>
    <div class="card" style="left:38px;top:104px;width:182px;height:180px">
      <div style="left:18px;top:4px;font-size:40px;font-weight:700;letter-spacing:1px">10:10</div>
      <div style="left:136px;top:12px;font-size:7px;font-weight:500;line-height:8px">AM<br>PM</div>
      <svg style="left:35px;top:57px;width:112px;height:112px" viewBox="0 0 112 112">
        <circle cx="56" cy="56" r="56" fill="#FFC000"/>
        <g font-family="Roboto,Arial,sans-serif" font-size="8" text-anchor="middle" fill="#1a1a1a">
          <text x="56" y="13">12</text><text x="81" y="20">1</text><text x="98" y="38">2</text><text x="103" y="59">3</text><text x="97" y="81">4</text><text x="81" y="98">5</text><text x="56" y="106">6</text><text x="31" y="98">7</text><text x="15" y="81">8</text><text x="9" y="59">9</text><text x="15" y="38">10</text><text x="31" y="20">11</text>
        </g>
        <path d="M56 56L22 38M56 56L48 30" stroke="#1a1a1a" stroke-width="1.2" stroke-linecap="round"/>
        <circle cx="56" cy="56" r="2" fill="#1a1a1a"/>
      </svg>
    </div>
    <div class="small-label" style="top:300px">Select Days of Week</div>
    <div class="day day--off" style="left:28px;width:24px">Sun</div>
    <div class="day day--on" style="left:57px;width:27px">Mon</div>
    <div class="day day--on" style="left:87px;width:25px">Tue</div>
    <div class="day day--on" style="left:115px;width:27px">Wed</div>
    <div class="day day--on" style="left:145px;width:26px">Thu</div>
    <div class="day day--on" style="left:174px;width:25px">Fri</div>
    <div class="day day--off" style="left:204px;width:24px">Sat</div>
    <div class="btn" style="left:63px;top:366px;width:130px">Add Time</div>
    <nav class="nav">
      <svg class="ico" style="left:118px"><use href="#i-siren"/></svg>
      <svg class="ico" style="left:186px"><use href="#i-speaker"/></svg>
    </nav>
    <div class="nav-active" style="left:41px"><svg><use href="#i-watch"/></svg></div>
    <div class="home-bar" style="background:#666"></div>
  </section>

  <!-- Motorised siren dashboard -->
  <section class="screen" style="left:46px;top:1241px">
    <div class="status"><span class="time">9:41</span><svg class="sys"><use href="#i-sys"/></svg></div>
    <div class="title" style="top:38px">Motorised Siren</div>
    <div class="hero" style="top:108px"><svg><use href="#i-siren"/></svg><span class="tap">Tap here!!</span></div>
    <div class="slider" style="left:24px;top:262px;width:206px">
      <span class="fill" style="width:150px"></span>
      <span class="knob" style="left:144px"><svg><use href="#i-speaker-fill"/></svg></span>
    </div>
    <div class="small-label" style="top:302px">Select a Device/group</div>
    <div style="left:42px;top:316px;width:172px"><span class="select" style="text-align:center;padding-left:0">Motorised siren 1<svg><use href="#i-caret"/></svg></span></div>
    <div class="plus"><svg><use href="#i-plus"/></svg></div>
    <nav class="nav">
      <svg class="ico" style="left:48px"><use href="#i-watch"/></svg>
      <svg class="ico" style="left:186px"><use href="#i-speaker"/></svg>
    </nav>
    <div class="nav-active" style="left:111px"><svg><use href="#i-siren"/></svg></div>
    <div class="home-bar" style="background:#666"></div>
  </section>

  <!-- Add motorised siren -->
  <section class="screen" style="left:334px;top:1241px">
    <div class="status"><span class="time">9:41</span><svg class="sys"><use href="#i-sys"/></svg></div>
    <div class="title" style="top:38px">Add Motorised Siren</div>
    <svg class="close" style="right:8px"><use href="#i-close"/></svg>
    <svg style="left:97px;top:80px;width:64px;height:64px"><use href="#i-siren"/></svg>
    <div class="field" style="top:171px;left:33px"><span class="label">Device name</span><span class="input">Enter Device name...</span></div>
    <div class="field" style="top:212px;left:33px"><span class="label">Device ID</span><span class="input">Enter device ID...</span></div>
    <div class="field" style="top:253px;left:33px"><span class="label">Location of device</span><span class="input">Enter location of the device...</span></div>
    <div class="field" style="top:294px;left:33px"><span class="label">Select a group</span><span class="select">Device group 1<svg><use href="#i-caret"/></svg></span></div>
    <div class="btn" style="left:63px;top:385px;width:130px">Add Now</div>
    <nav class="nav">
      <svg class="ico" style="left:48px"><use href="#i-watch"/></svg>
      <svg class="ico" style="left:186px"><use href="#i-speaker"/></svg>
    </nav>
    <div class="nav-active" style="left:111px"><svg><use href="#i-siren"/></svg></div>
    <div class="home-bar" style="background:#666"></div>
  </section>

  <!-- Speaker dashboard -->
  <section class="screen" style="left:46px;top:1861px">
    <div class="status"><span class="time">9:41</span><svg class="sys"><use href="#i-sys"/></svg></div>
    <div class="title" style="top:38px">Speaker</div>
    <div class="hero" style="top:90px"><svg><use href="#i-speaker"/></svg><span class="tap">Tap here!!</span></div>
    <div class="slider" style="left:20px;top:245px;width:208px">
      <span class="fill" style="width:150px"></span>
      <span class="knob" style="left:144px"><svg><use href="#i-speaker-fill"/></svg></span>
    </div>
    <div class="small-label" style="top:277px">Select a Device/group</div>
    <div style="left:42px;top:291px;width:172px"><span class="select" style="text-align:center;padding-left:0">Audio group 1<svg><use href="#i-caret"/></svg></span></div>
    <div class="tile tile--on" style="left:41px"><svg><use href="#i-note"/></svg><span>Upload mp3</span></div>
    <div class="tile" style="left:103px"><svg><use href="#i-mic"/></svg><span>Record audio</span></div>
    <div class="tile" style="left:164px"><svg><use href="#i-tts"/></svg><span>Text to speech</span></div>
    <div class="plus"><svg><use href="#i-plus"/></svg></div>
    <nav class="nav">
      <svg class="ico" style="left:48px"><use href="#i-watch"/></svg>
      <svg class="ico" style="left:118px"><use href="#i-siren"/></svg>
    </nav>
    <div class="nav-active" style="left:179px"><svg><use href="#i-speaker"/></svg></div>
    <div class="home-bar" style="background:#666"></div>
  </section>

  <!-- Upload mp3 -->
  <section class="screen" style="left:334px;top:1861px">
    <div class="status"><span class="time">9:41</span><svg class="sys"><use href="#i-sys"/></svg></div>
    <div class="title" style="top:38px">Upload mp3 file</div>
    <svg class="close"><use href="#i-close"/></svg>
    <svg style="left:104px;top:138px;width:50px;height:50px"><use href="#i-note"/></svg>
    <div style="left:40px;top:239px;width:175px;height:23px;border-radius:12px;box-shadow:inset 0 0 0 1px var(--line),0 1px 2px rgba(0,0,0,.1);font-size:9px;color:var(--muted);line-height:23px;text-align:center">Browse from device<svg style="right:10px;top:6px;width:11px;height:11px;color:#777"><use href="#i-upload"/></svg></div>
    <div class="wave" style="top:282px"><svg class="play"><use href="#i-play"/></svg><svg class="bars"><rect width="172" height="14" fill="url(#wave-bars)"/></svg><span class="dur">2:09</span></div>
    <div class="caption" style="top:301px">sound1.mp3</div>
    <div class="btn" style="left:63px;top:330px;width:130px">Upload</div>
    <nav class="nav">
      <svg class="ico" style="left:48px"><use href="#i-watch"/></svg>
      <svg class="ico" style="left:118px"><use href="#i-siren"/></svg>
    </nav>
    <div class="nav-active" style="left:179px"><svg><use href="#i-speaker"/></svg></div>
    <div class="home-bar" style="background:#666"></div>
  </section>

  <!-- Record audio -->
  <section class="screen" style="left:622px;top:1861px">
    <div class="status"><span class="time">9:41</span><svg class="sys"><use href="#i-sys"/></svg></div>
    <div class="title" style="top:38px">Record Audio</div>
    <svg class="close"><use href="#i-close"/></svg>
    <div style="left:92px;top:136px;width:72px;height:72px;border-radius:50%;background:var(--yellow);box-shadow:0 0 0 3px #fff,0 0 0 4px var(--line),0 3px 6px rgba(0,0,0,.2)"><svg style="left:18px;top:16px;width:36px;height:38px"><use href="#i-mic"/></svg></div>
    <div class="caption" style="top:212px">Tap to record.</div>
    <div class="wave" style="top:282px"><svg class="play"><use href="#i-play"/></svg><svg class="bars"><rect width="172" height="14" fill="url(#wave-bars)"/></svg><span class="dur">2:09</span></div>
    <div class="caption" style="top:301px">Recording1.aac</div>
    <div class="btn" style="left:63px;top:330px;width:130px">Send to speaker</div>
    <nav class="nav">
      <svg class="ico" style="left:48px"><use href="#i-watch"/></svg>
      <svg class="ico" style="left:118px"><use href="#i-siren"/></svg>
    </nav>
    <div class="nav-active" style="left:179px"><svg><use href="#i-speaker"/></svg></div>
    <div class="home-bar" style="background:#666"></div>
  </section>

  <!-- Text to speech -->
  <section class="screen" style="left:910px;top:1861px">
    <div class="status"><span class="time">9:41</span><svg class="sys"><use href="#i-sys"/></svg></div>
    <div class="title" style="top:38px">Text to Speech</div>
    <svg class="close"><use href="#i-close"/></svg>
    <svg style="left:103px;top:82px;width:50px;height:50px"><use href="#i-tts"/></svg>
    <div class="tts-box"><p>Hello everyone,<br>this is to inform you all that this message is being sent as a mock drill...</p></div>
    <div class="wave" style="top:314px"><svg class="play"><use href="#i-play"/></svg><svg class="bars"><rect width="172" height="14" fill="url(#wave-bars)"/></svg><span class="dur">2:09</span></div>
    <div class="kb">
      <div class="suggest"><span class="pick">“The”</span><span>the</span><span>to</span></div>
      <div class="row" style="top:33px"><span class="key">q</span><span class="key">w</span><span class="key">e</span><span class="key">r</span><span class="key">t</span><span class="key">y</span><span class="key">u</span><span class="key">i</span><span class="key">o</span><span class="key">p</span></div>
      <div class="row" style="top:68px"><span class="key">a</span><span class="key">s</span><span class="key">d</span><span class="key">f</span><span class="key">g</span><span class="key">h</span><span class="key">j</span><span class="key">k</span><span class="key">l</span></div>
      <div class="row" style="top:103px"><span class="key key--fn">⇧</span><span class="key">z</span><span class="key">x</span><span class="key">c</span><span class="key">v</span><span class="key">b</span><span class="key">n</span><span class="key">m</span><span class="key key--fn">⌫</span></div>
      <div class="row" style="top:139px"><span class="key key--action">ABC</span><span class="key key--wide">space</span><span class="key key--action">return</span></div>
      <svg class="extra" style="left:12px" viewBox="0 0 24 24"><g fill="none" stroke="currentColor" stroke-width="1.6" stroke-linecap="round"><circle cx="12" cy="12" r="9"/><path d="M8 14a5 5 0 0 0 8 0"/><path d="M9 9.5h.01M15 9.5h.01" stroke-width="2.4"/></g></svg>
      <svg class="extra" style="left:227px"><use href="#i-mic"/></svg>
    </div>
    <div class="home-bar" style="background:#1a1a1a;width:92px"></div>
  </section>

  <!-- Add speaker -->
  <section class="screen" style="left:1198px;top:1861px">
    <div class="status"><span class="time">9:41</span><svg class="sys"><use href="#i-sys"/></svg></div>
    <div class="title" style="top:38px">Add Speaker</div>
    <svg class="close"><use href="#i-close"/></svg>
    <svg style="left:94px;top:80px;width:68px;height:68px"><use href="#i-speaker"/></svg>
    <div class="field" style="top:169px;left:33px"><span class="label">Device name</span><span class="input">Enter Device name...</span></div>
    <div class="field" style="top:210px;left:33px"><span class="label">Device ID</span><span class="input">Enter device ID...</span></div>
    <div class="field" style="top:251px;left:33px"><span class="label">Location of device</span><span class="input">Enter location of the device...</span></div>
    <div class="field" style="top:292px;left:33px"><span class="label">Select a group</span><span class="select">Device group 1<svg><use href="#i-caret"/></svg></span></div>
    <div class="btn" style="left:63px;top:385px;width:130px">Add Now</div>
    <nav class="nav">
      <svg class="ico" style="left:48px"><use href="#i-watch"/></svg>
      <svg class="ico" style="left:118px"><use href="#i-siren"/></svg>
    </nav>
    <div class="nav-active" style="left:179px"><svg><use href="#i-speaker"/></svg></div>
    <div class="home-bar" style="background:#666"></div>
  </section>

  <div class="feature-mark" style="position:absolute">Varelko</div>

</main>
</body>
</html>
```